BrivoTerna. Lantern of the Steady Harvest. Business card

Professional business card for BrivoTerna (Lantern of the Steady Harvest)
My rationale: Strategy-> Execution-> Results-> Value that lead to the BrivoTerna name: We put the Lantern of the Steady Harvest.
We deliver value to our customers helping them at defining a good strategy (cyan arrow). 90% of well formulated strategies fail due to poor execution so we also consider strategical execution very important (green arrow). Due to the execution we obtain the results (blue arrow). Finally, the results provide feedback to redefine strategy, and the new strategy has to be executed and new results obtained providing new feedback and on and on. It's like a wheel that finally, must create corporate value: value for shareholders, staholders, employees, providers...-

Target Market(s)

CEOs and steering comitees , invewrnent funds

Industry/Entity Type

Business Consultant

Contact Information for Business Card

Teodoro Vinsquel
CEO & Founder
teodoro.vinsquel@brivoterna-example.com
Mobile: +34 655.803.912
www.brivoterna-example.com

Colors

Designer to choose colors to be used in the design.

Requirements
Nice to have
• Nice to hace the words: Strategy, execution, results
• Nice to vave the claim: Lantern of the Steady Harvest
• The three colors should be shown:
• cyan for STRATEGY
• green for EXECUTION
• blue for RESULTS
Should not have
• Complete black background

```html
<!DOCTYPE html>
<html lang="en">
<head>
<meta charset="utf-8">
<title>BrivoTerna – Business Card</title>
<link rel="stylesheet" href="https://fonts.googleapis.com/css2?family=Roboto:wght@400;700&display=swap">
<style>
  :root {
    --bg: #9d9d9f;
    --navy: #02339a;
    --navy-soft: #1c47a3;
    --cyan: #00b1ec;
    --green: #9acc35;
    --white: #ffffff;
  }
  * { margin: 0; padding: 0; box-sizing: border-box; }
  html, body {
    width: 1200px; height: 900px; overflow: hidden;
    background: var(--bg);
    font-family: "Roboto", Arial, sans-serif;
  }
  .card {
    position: absolute;
    left: 363px;
    width: 475px;
    height: 271px;
    overflow: hidden;
  }
  .card--front { top: 145px; background: var(--navy); }
  .card--back  { top: 484px; background: var(--white); }

  .value-bands {
    position: absolute;
    display: block;
  }
  .card--front .value-bands { left: 0; top: 120px; width: 240px; height: 151px; }
  .card--back .value-bands  { left: 232px; top: 120px; width: 243px; height: 151px; }

  .wordmark {
    position: absolute;
    font-weight: 700;
    font-size: 44px;
    letter-spacing: -1.5px;
    line-height: 1;
    white-space: nowrap;
  }
  .card--front .wordmark {
    right: 30px; top: 206px;
    color: var(--white);
    display: flex; align-items: center; gap: 10px;
  }
  .wordmark__dot {
    width: 14px; height: 14px; border-radius: 50%;
    background: var(--white);
  }
  .card--back .wordmark {
    left: 24px; top: 32px;
    color: var(--navy);
  }

  .contact {
    position: absolute;
    left: 25px; top: 142px;
    color: var(--navy);
  }
  .contact__name {
    font-size: 16.5px; font-weight: 700; color: var(--cyan);
    line-height: 19px;
  }
  .contact__role { font-size: 11.5px; line-height: 14px; }
  .contact__rule {
    width: 19px; height: 1px; background: var(--navy);
    margin: 9px 0 9px;
  }
  .contact__list { list-style: none; font-size: 11.5px; }
  .contact__list li {
    display: flex; align-items: center; gap: 5px;
    height: 18px;
  }
  .contact__list svg { width: 9px; height: 9px; flex: none; }
</style>
</head>
<body>

<section class="card card--front" aria-label="Card front">
  <svg class="value-bands" viewBox="0 0 240 151" role="img" aria-label="Faint brand bands: strategy, execution, results">
    <rect x="0" y="0" width="240" height="38" fill="#1c47a3"/>
    <rect x="0" y="55" width="220" height="38" fill="#1c47a3"/>
    <rect x="0" y="110" width="190" height="41" fill="#1c47a3"/>
  </svg>
  <div class="wordmark"><span class="wordmark__dot"></span>BrivoTerna</div>
</section>

<section class="card card--back" aria-label="Card back">
  <div class="wordmark">BrivoTerna</div>

  <svg class="value-bands" viewBox="0 0 243 151" role="img" aria-label="Brand bands: results in blue, execution in green, strategy in cyan">
    <rect x="10" y="0" width="233" height="38" fill="#02339a"/>
    <rect x="20" y="56" width="223" height="38" fill="#9acc35"/>
    <rect x="35" y="112" width="208" height="39" fill="#00b1ec"/>
  </svg>

  <div class="contact">
    <p class="contact__name">Teodoro Vinsquel</p>
    <p class="contact__role">CEO &amp; Founder</p>
    <div class="contact__rule"></div>
    <ul class="contact__list">
      <li>
        <svg viewBox="0 0 10 10" aria-hidden="true"><path fill="#00b1ec" d="M2 0.5 L3.6 2.6 L2.8 3.6 Q4 6 6.4 7.2 L7.4 6.4 L9.5 8 L8.4 9.5 Q4.5 9.5 2 7 Q0.5 4.5 0.5 1.6 Z"/></svg>
        <span>+34 655.803.912</span>
      </li>
      <li>
        <svg viewBox="0 0 10 10" aria-hidden="true"><circle cx="5" cy="5" r="4.5" fill="#00b1ec"/><path d="M0.5 5 H9.5 M5 0.5 Q2.5 5 5 9.5 M5 0.5 Q7.5 5 5 9.5" stroke="#fff" stroke-width="0.7" fill="none"/></svg>
        <span>www.brivoterna-example.com</span>
      </li>
      <li>
        <svg viewBox="0 0 10 10" aria-hidden="true"><rect x="0" y="2" width="10" height="6.5" fill="#00b1ec"/><path d="M0.3 2.3 L5 6 L9.7 2.3" stroke="#fff" stroke-width="0.8" fill="none"/></svg>
        <span>teodoro.vinsquel@brivoterna-example.com</span>
      </li>
    </ul>
  </div>
</section>

</body>
</html>
```